LHP Regal Business Card Design 2020

Your Manor Steward is looking for a business card that is clean and straight to the point but still looks high-end and attractive. We are a team comprised of management and field professionals focused on the high-end residential marketplace. We serve homeowners and trade professionals directly based out of the Metrowest/Boston area. We provide client services as well as construction/renovation services.
We are aiming for a black and white feel (white background and black text) and a matte finish with rounded edges.

We want to emphasis our vision of "Properties - Projects - Partners".
Dana Pellham is the president of LHP

Please include the following areas we service: Boston/Cape/Newport
Please make sure to include Dana's mobile (555) 213 4480 & office number (555) 640 1937, email dana@yourmanorsteward.example and website www.yourmanorsteward.example

Colors

Designer to choose only greyscale colors for use in the design.

Requirements
Must have
• Include "Properties - Projects - Partners" in design

Include "After Hours Emergency Support # 1800 555 0142" with icon

```html
<!DOCTYPE html>
<html lang="en">
<head>
<meta charset="utf-8">
<title>LHP Business Card</title>
<link href="https://fonts.googleapis.com/css2?family=Josefin+Sans:wght@300;400&family=Montserrat:wght@600&display=swap" rel="stylesheet">
<style>
  :root {
    --backdrop: #e6e6e6;
    --paper: #f7f7f7;
    --ink: #2b2b2b;
    --ink-soft: #8a8a8a;
    --rule: #9a9a9a;
    --card-dark: #2d2d2d;
    --on-dark: #ececec;
    --on-dark-soft: #b5b5b5;
  }
  * { box-sizing: border-box; margin: 0; padding: 0; }
  html, body { width: 1200px; height: 801px; overflow: hidden; }
  body {
    background: var(--backdrop);
    display: flex;
    align-items: center;
    justify-content: center;
    gap: 40px;
  }
  .card {
    width: 520px;
    height: 297px;
    border-radius: 14px;
    position: relative;
    box-shadow: 0 6px 18px rgba(0,0,0,.12);
  }
  .card--contact { background: var(--paper); color: var(--ink); }
  .card--brand {
    background: var(--card-dark);
    color: var(--on-dark);
    display: flex;
    flex-direction: column;
    align-items: center;
    justify-content: center;
  }
  .brand-mark {
    font-family: "Montserrat", sans-serif;
    font-weight: 600;
    line-height: 1;
  }
  .card--contact .brand {
    position: absolute;
    top: 26px;
    right: 34px;
    text-align: center;
  }
  .card--contact .brand-mark { font-size: 72px; letter-spacing: 1px; }
  .brand-name {
    font-family: "Montserrat", sans-serif;
    font-weight: 600;
    text-transform: uppercase;
    font-size: 12px;
    letter-spacing: 2.6px;
    margin-top: 8px;
  }
  .card--brand .brand-mark { font-size: 112px; letter-spacing: 2px; }
  .card--brand .brand-name { font-size: 16px; letter-spacing: 3.4px; margin-top: 14px; }
  .vision {
    font-family: "Josefin Sans", sans-serif;
    font-weight: 300;
    font-size: 12px;
    letter-spacing: 2px;
    text-transform: uppercase;
    color: var(--on-dark-soft);
    margin-top: 14px;
  }
  .name-row {
    position: absolute;
    left: 34px;
    right: 30px;
    top: 156px;
    display: flex;
    align-items: flex-end;
    gap: 10px;
  }
  .person-name {
    font-family: "Josefin Sans", sans-serif;
    font-weight: 400;
    font-size: 17px;
    letter-spacing: 1.6px;
    text-transform: uppercase;
    white-space: nowrap;
  }
  .name-rule { flex: 1; height: 1px; background: var(--rule); margin-bottom: 5px; }
  .person-title {
    position: absolute;
    left: 34px;
    top: 182px;
    font-family: "Josefin Sans", sans-serif;
    font-weight: 300;
    font-size: 13px;
    color: var(--ink-soft);
  }
  .contact-list {
    position: absolute;
    left: 34px;
    top: 206px;
    list-style: none;
    font-family: "Josefin Sans", sans-serif;
    font-weight: 300;
    font-size: 13px;
    color: var(--ink-soft);
  }
  .contact-list li { display: flex; align-items: center; gap: 8px; height: 21px; }
  .contact-icon { width: 13px; height: 13px; flex: none; }
  .side-info {
    position: absolute;
    right: 30px;
    top: 182px;
    text-align: right;
    font-family: "Josefin Sans", sans-serif;
    font-weight: 300;
    font-size: 12px;
    color: var(--ink-soft);
    line-height: 21px;
  }
  .website { letter-spacing: .4px; }
  .website strong { font-weight: 400; color: var(--ink); }
  .service-areas { letter-spacing: .6px; }
  .emergency {
    display: flex;
    align-items: center;
    justify-content: flex-end;
    gap: 8px;
    margin-top: 2px;
    line-height: 15px;
  }
  .emergency strong { font-weight: 400; color: var(--ink); }
  .emergency-icon { width: 22px; height: 22px; flex: none; }
</style>
</head>
<body>
  <section class="card card--contact">
    <div class="brand">
      <div class="brand-mark">LHP</div>
      <div class="brand-name">Your Manor Steward</div>
    </div>
    <div class="name-row">
      <span class="person-name">Dana Pellham</span>
      <span class="name-rule"></span>
    </div>
    <p class="person-title">President of LHP</p>
    <ul class="contact-list">
      <li>
        <svg class="contact-icon" viewBox="0 0 14 14" aria-hidden="true">
          <circle cx="7" cy="7" r="7" fill="#2b2b2b"/>
          <path d="M4.2 5.6c.6-1 1.6-1.4 2.8-1.4s2.2.4 2.8 1.4l-.9.6-.6-.9H5.7l-.6.9zM4.8 6.6h4.4l.6 3.2H4.2z" fill="#f7f7f7"/>
        </svg>
        <span>(555) 640 1937</span>
      </li>
      <li>
        <svg class="contact-icon" viewBox="0 0 14 14" aria-hidden="true">
          <circle cx="7" cy="7" r="7" fill="#2b2b2b"/>
          <rect x="4.8" y="3.4" width="4.4" height="7.2" rx=".8" fill="none" stroke="#f7f7f7" stroke-width="1"/>
        </svg>
        <span>(555) 213 4480</span>
      </li>
      <li>
        <svg class="contact-icon" viewBox="0 0 14 14" aria-hidden="true">
          <circle cx="7" cy="7" r="7" fill="#2b2b2b"/>
          <rect x="3.6" y="4.6" width="6.8" height="4.8" fill="none" stroke="#f7f7f7" stroke-width=".9"/>
          <path d="M3.6 4.6 7 7.4l3.4-2.8" fill="none" stroke="#f7f7f7" stroke-width=".9"/>
        </svg>
        <span>dana@yourmanorsteward.example</span>
      </li>
    </ul>
    <div class="side-info">
      <p class="website">www.<strong>yourmanorsteward</strong>.example</p>
      <p class="service-areas">Boston / Cape / Newport</p>
      <div class="emergency">
        <svg class="emergency-icon" viewBox="0 0 22 22" aria-hidden="true">
          <circle cx="11" cy="11" r="11" fill="#2b2b2b"/>
          <path d="M7.2 6.2c.5-.5 1.2-.4 1.5.1l1 1.6c.3.5.2 1-.2 1.3l-.6.5c.6 1.3 1.6 2.3 2.9 2.9l.5-.6c.3-.4.8-.5 1.3-.2l1.6 1c.5.3.6 1 .1 1.5l-.7.7c-.6.6-1.6.7-2.5.3-2.3-1-4.1-2.8-5.1-5.1-.4-.9-.3-1.9.3-2.5z" fill="#f7f7f7"/>
        </svg>
        <span>After Hours Emergency Support<br><strong># 1800 555 0142</strong></span>
      </div>
    </div>
  </section>

  <section class="card card--brand">
    <div class="brand-mark">LHP</div>
    <div class="brand-name">Your Manor Steward</div>
    <p class="vision">Properties - Projects - Partners</p>
  </section>
</body>
</html>
```